Business Card Design

We are a manufacturing and distribution company with most of our customer base being supermarkets. We have established brand guidelines that are attached.

```html
<!DOCTYPE html>
<html lang="en">
<head>
<meta charset="UTF-8">
<title>Varento Business Card</title>
<link rel="stylesheet" href="https://fonts.googleapis.com/css2?family=Poppins:wght@400;600;700&display=swap">
<style>
  :root {
    --brand-red: #e31b23;
    --brand-blue: #006aad;
    --ink: #231f20;
    --paper: #ffffff;
    --backdrop: #d9d9d9;
    --rule: rgba(255,255,255,0.55);
  }
  * { margin: 0; padding: 0; box-sizing: border-box; }
  html, body { width: 1200px; height: 1200px; overflow: hidden; }
  body {
    background: var(--backdrop);
    position: relative;
    font-family: "Poppins", sans-serif;
  }
  .card {
    position: absolute;
    top: 303px;
    width: 370px;
    height: 594px;
    overflow: hidden;
  }
  /* Front */
  .card-front { left: 200px; background: var(--brand-blue); }
  .card-front .half-red {
    position: absolute; left: 0; top: 0; bottom: 0; width: 178px;
    background: var(--brand-red);
  }
  .card-front .front-name {
    position: absolute; left: 0; right: 0; top: 296px;
    transform: translateY(-50%);
    text-align: center;
    color: var(--paper);
    font-weight: 700;
    font-size: 56px;
    letter-spacing: 1px;
    line-height: 1;
  }
  /* Back */
  .card-back { left: 599px; background: var(--brand-blue); color: var(--paper); }
  .brand-area {
    position: absolute; left: 0; top: 0; width: 100%; height: 287px;
    background: var(--paper);
  }
  .brand-square {
    position: absolute; left: 167px; top: 96px; width: 36px; height: 36px;
    background: var(--brand-red);
  }
  .brand-name {
    position: absolute; left: 0; right: 0; top: 194px;
    transform: translateY(-50%);
    text-align: center;
    color: var(--ink);
    font-weight: 700;
    font-size: 50px;
    letter-spacing: 1px;
    line-height: 1;
  }
  .divider-band { position: absolute; left: 0; top: 287px; width: 100%; height: 40px; }
  .contact { position: absolute; left: 0; right: 0; text-align: center; line-height: 1; }
  .person-name { top: 339px; font-size: 25px; font-weight: 700; letter-spacing: 0.5px; }
  .person-role { top: 366px; font-size: 16px; font-weight: 400; }
  .icon-row {
    position: absolute; left: 0; top: 396px; width: 100%; height: 25px;
  }
  .icon-row .line {
    position: absolute; top: 12px; height: 1px; background: var(--rule);
  }
  .icon-box {
    position: absolute; top: 0; width: 25px; height: 25px;
    background: var(--paper); border-radius: 3px;
  }
  .icon-box svg { display: block; width: 25px; height: 25px; }
  .detail { font-size: 17px; font-weight: 400; }
  .rule {
    position: absolute; left: 88px; width: 194px; top: 506px; height: 1px; background: var(--rule);
  }
</style>
</head>
<body>

<section class="card card-front" aria-label="Card front">
  <div class="half-red"></div>
  <div class="front-name">VARENTO</div>
</section>

<section class="card card-back" aria-label="Card back">
  <div class="brand-area">
    <div class="brand-square"></div>
    <div class="brand-name">VARENTO</div>
  </div>

  <svg class="divider-band" viewBox="0 0 364 40" width="364" height="40">
    <rect x="0" y="0" width="364" height="7" fill="var(--brand-red)"/>
    <polygon points="143,7 227,7 186,36" fill="var(--brand-red)"/>
  </svg>

  <div class="contact person-name">DANIEL HARPER</div>
  <div class="contact person-role">Managing Director</div>

  <div class="icon-row">
    <div class="line" style="left:87px;width:53px"></div>
    <div class="icon-box" style="left:142px">
      <svg viewBox="0 0 25 25" aria-hidden="true">
        <path d="M6 10c0-3 3-4 6.5-4s6.5 1 6.5 4l-2.5 0.5-0.5-2h-7l-0.5 2z" fill="var(--brand-blue)"/>
        <rect x="8" y="11" width="9" height="7" rx="1" fill="var(--brand-blue)"/>
      </svg>
    </div>
    <div class="icon-box" style="left:170px">
      <svg viewBox="0 0 25 25" aria-hidden="true">
        <rect x="5" y="7.5" width="15" height="10" fill="none" stroke="var(--brand-blue)" stroke-width="1.6"/>
        <path d="M5 7.5l7.5 6 7.5-6" fill="none" stroke="var(--brand-blue)" stroke-width="1.4"/>
      </svg>
    </div>
    <div class="icon-box" style="left:198px">
      <svg viewBox="0 0 25 25" aria-hidden="true">
        <circle cx="12.5" cy="12.5" r="7" fill="var(--brand-blue)"/>
        <path d="M9 9c2 0 2 2 4 2s1 3-1 3-1 2-2 2M15 7.5c0 2 2 2 3 3" fill="none" stroke="var(--paper)" stroke-width="1.2"/>
      </svg>
    </div>
    <div class="line" style="left:230px;width:46px"></div>
  </div>

  <div class="contact detail" style="top:429px">044-987 654 321</div>
  <div class="contact detail" style="top:450px">hello@varento.com</div>
  <div class="contact detail" style="top:471px">www.varento.com</div>

  <div class="rule"></div>

  <div class="contact detail" style="top:522px">17, Harbour Trade Park</div>
  <div class="contact detail" style="top:543px">60318, Northland</div>
</section>

</body>
</html>
```